Business card for law firm

Need business card for new law firm. Think confident, authoritative, conservative, but not stuffy or old-fashioned.

Contact Information for Business Card

Content for card - logo (uploaded), plus the following:

Paul Whitcombe (larger font)
Managing Partner (larger font, but not as large as name)
Level 9, 7 Ferris Lane
Sydney NSW 2000
Main Tel 02 9364 2710
Direct Tel 02 8472 3159
Email paul@qvlegal.com.au
www.qvlegal.com.au

Letterhead design should include logo plus:
Level 9, 7 Ferris Lane
Sydney NSW 2000
Tel 02 8472 3159
www.qvlegal.com.au

```html
<!DOCTYPE html>
<html lang="en">
<head>
<meta charset="utf-8">
<title>Quayvale Legal — Business Card</title>
<link rel="stylesheet" href="https://fonts.googleapis.com/css2?family=Open+Sans:wght@400;700&display=swap">
<style>
  :root {
    --navy: #0f1f58;
    --ink: #1b1b1b;
    --card-white: #ffffff;
    --card-black: #050505;
    --stage-light: #ececed;
    --stage-dark: #c6c7ca;
    --rule-grey: #c9c9c9;
  }
  * { margin: 0; padding: 0; box-sizing: border-box; }
  html, body { width: 1200px; height: 1113px; overflow: hidden; }
  body {
    position: relative;
    background: linear-gradient(135deg, var(--stage-light) 0%, var(--stage-dark) 100%);
    font-family: "Open Sans", Arial, sans-serif;
  }
  .card {
    position: absolute;
    width: 768px;
    height: 437px;
    overflow: hidden;
  }
  .card--front {
    left: 351px; top: 80px;
    background: var(--card-white);
    border: 1px solid #b5b5b5;
    border-radius: 24px;
  }
  .card--back {
    left: 76px; top: 581px;
    background: var(--card-black);
    border-radius: 40px;
  }
  .brand {
    position: absolute;
    display: flex;
    flex-direction: column;
    align-items: center;
  }
  .brand__mark { display: block; }
  .brand__name {
    font-family: "Open Sans", Arial, sans-serif;
    font-weight: 400;
    line-height: 1;
    white-space: nowrap;
  }

  .card--front .brand { left: 40px; width: 400px; top: 80px; color: var(--ink); }
  .card--front .brand__mark { width: 82px; height: 82px; background: var(--navy); margin-bottom: 60px; }
  .card--front .brand__name { font-size: 36px; }

  .divider {
    position: absolute;
    left: 432px; top: 78px;
    width: 2px; height: 220px;
    background: var(--rule-grey);
  }
  .contact { position: absolute; left: 461px; top: 72px; }
  .contact__name {
    color: var(--navy);
    font-weight: 700;
    font-size: 26px;
    line-height: 1.2;
  }
  .contact__role {
    color: #333;
    font-size: 20px;
    margin-top: 8px;
    letter-spacing: 0.3px;
  }
  .contact__list { list-style: none; margin-top: 24px; }
  .contact__item {
    display: flex;
    align-items: center;
    gap: 7px;
    font-size: 20px;
    color: #222;
    height: 34px;
  }
  .contact__icon { width: 17px; height: 17px; flex: none; }

  .address-band {
    position: absolute;
    left: 0; right: 0; top: 349px;
    height: 52px;
    border-top: 2px solid #333;
    border-bottom: 2px solid #333;
    padding: 3px 0;
  }
  .address-band__fill {
    height: 100%;
    background: var(--navy);
    color: #fff;
    font-size: 20px;
    display: flex;
    align-items: center;
    justify-content: center;
  }

  .card--back .brand { left: 0; right: 0; top: 75px; color: #fff; }
  .card--back .brand__mark { width: 90px; height: 90px; background: #fff; margin-bottom: 66px; }
  .card--back .brand__name { font-size: 46px; }
  .web {
    position: absolute;
    left: 0; right: 0; top: 366px;
    text-align: center;
    color: #fff;
    font-size: 25px;
    letter-spacing: 4px;
    line-height: 1;
  }
  .web strong { font-weight: 700; }
</style>
</head>
<body>

<section class="card card--front" aria-label="Business card front">
  <div class="brand">
    <span class="brand__mark" aria-hidden="true"></span>
    <span class="brand__name">Quayvale Legal</span>
  </div>

  <div class="divider"></div>

  <div class="contact">
    <p class="contact__name">PAUL WHITCOMBE</p>
    <p class="contact__role">MANAGING PARTNER</p>
    <ul class="contact__list">
      <li class="contact__item">
        <svg class="contact__icon" viewBox="0 0 20 20" aria-hidden="true"><circle cx="10" cy="10" r="8.5" fill="none" stroke="#0f1f58" stroke-width="1.6"/><path d="M7 5.5c-1.5 1-1.3 4 .8 6.4s4.6 3.3 5.9 2.1l-1.5-2-1.4.7c-.9-.4-2-1.8-2.3-2.8l1.1-1z" fill="#0f1f58"/></svg>
        02 9364 2710(Main)
      </li>
      <li class="contact__item">
        <svg class="contact__icon" viewBox="0 0 20 20" aria-hidden="true"><circle cx="10" cy="10" r="8.5" fill="none" stroke="#0f1f58" stroke-width="1.6"/><path d="M7 5.5c-1.5 1-1.3 4 .8 6.4s4.6 3.3 5.9 2.1l-1.5-2-1.4.7c-.9-.4-2-1.8-2.3-2.8l1.1-1z" fill="#0f1f58"/></svg>
        02 8472 3159(Direct)
      </li>
      <li class="contact__item">
        <svg class="contact__icon" viewBox="0 0 20 20" aria-hidden="true"><path d="M2 8l8-5 8 5v9H2z" fill="#0f1f58"/><path d="M4 8.5l6 4 6-4" fill="none" stroke="#fff" stroke-width="1.4"/></svg>
        paul@qvlegal.com.au
      </li>
      <li class="contact__item">
        <svg class="contact__icon" viewBox="0 0 20 20" aria-hidden="true"><g fill="none" stroke="#0f1f58" stroke-width="1.4"><circle cx="10" cy="10" r="8"/><ellipse cx="10" cy="10" rx="3.6" ry="8"/><path d="M2 10h16M3.5 5.8h13M3.5 14.2h13"/></g></svg>
        www.qvlegal.com.au
      </li>
    </ul>
  </div>

  <div class="address-band">
    <div class="address-band__fill">Level 9, 7 Ferris Lane, Sydney NSW 2000</div>
  </div>
</section>

<section class="card card--back" aria-label="Business card back">
  <div class="brand">
    <span class="brand__mark" aria-hidden="true"></span>
    <span class="brand__name">Quayvale Legal</span>
  </div>
  <p class="web">www.<strong>qvlegal</strong>.com.au</p>
</section>

</body>
</html>
```